Orvell Global Services - Partnership Proposal

My company ORV is a study abroad consultant and We want to send a proposal to Universities and Educational institutions to partner with us. This proposal shall be used by our marketing team to collaborate with more than 100 top universities of the world and hence it must look like an extremely professional presentation.

Target Market(s)

Education institutions and Universities

Industry/Entity Type

Education

Font styles to use
Serif

Colors

Designer to choose colors to be used in the design.

Requirements
Must have
• A professional and neat look with company logo.
Nice to have
• Would like to see some the text presented in an interesting eye catchy manner.
Should not have
• Should not have too many colours or different fonts

```html
<!DOCTYPE html>
<html lang="en">
<head>
<meta charset="utf-8">
<title>Orvell Global Services – Partnership Proposal</title>
<link href="https://fonts.googleapis.com/css2?family=Open+Sans:wght@400;700;800&family=Oswald:wght@500&display=swap" rel="stylesheet">
<style>
  :root {
    --purple: #762a79;
    --yellow: #fbb316;
    --ink: #222222;
    --white: #ffffff;
    --backdrop: #1c1c1c;
    --frame: #cfcfcf;
    --placeholder: #e6e6e6;
  }
  * { margin: 0; padding: 0; box-sizing: border-box; }
  html, body { width: 945px; height: 1200px; overflow: hidden; background: var(--backdrop); }
  body { position: relative; font-family: "Open Sans", Arial, sans-serif; }

  .flyer { position: absolute; left: 80px; top: 92px; width: 785px; height: 1015px; background: var(--white); overflow: hidden; }
  .flyer-shapes { position: absolute; inset: 0; }
  .abs { position: absolute; }

  .brand { right: 40px; top: 62px; display: flex; align-items: center; gap: 12px; }
  .brand-mark { width: 22px; height: 22px; background: var(--purple); flex: none; }
  .brand-name { font-weight: 800; font-size: 27px; line-height: 32px; color: var(--ink); letter-spacing: .5px; }

  .strap { right: 32px; top: 187px; font-family: "Oswald", Arial, sans-serif; font-weight: 500; font-size: 15px; color: var(--white); letter-spacing: .1px; }

  .headline { right: 31px; top: 256px; text-align: right; color: var(--white); font-weight: 800; font-size: 37px; line-height: 50px; }

  .intro { left: 50px; top: 434px; width: 710px; color: var(--white); font-size: 11.6px; line-height: 16.6px; letter-spacing: -0.15px; }

  .services { left: 394px; top: 560px; font-family: "Oswald", Arial, sans-serif; font-weight: 500; font-size: 21px; color: var(--white); display: flex; gap: 6px; }
  .services span { border-left: 3px solid var(--purple); padding-left: 6px; line-height: 24px; }

  .about { left: 47px; top: 626px; width: 360px; color: var(--ink); font-size: 11.8px; line-height: 16.8px; letter-spacing: -0.15px; }

  .tab { height: 24px; color: var(--white); font-weight: 700; font-size: 13.5px; line-height: 24px; padding-left: 7px; }
  .tab-why { left: 50px; top: 774px; width: 250px; background: var(--purple); clip-path: polygon(0 0, 92% 0, 100% 100%, 0 100%); }
  .tab-nz { left: 442px; top: 621px; width: 250px; background: var(--purple); clip-path: polygon(0 0, 94% 0, 100% 100%, 0 100%); }

  .reasons { left: 50px; top: 813px; list-style: none; }
  .reason { display: flex; align-items: center; height: 33px; margin-bottom: 14px; }
  .reason-icon { width: 33px; height: 33px; border: 2px solid var(--purple); border-radius: 7px; font-size: 6px; font-weight: 700; color: var(--purple); display: flex; align-items: center; justify-content: center; flex: none; }
  .reason-text { margin-left: 10px; color: var(--purple); font-weight: 700; font-size: 13.8px; line-height: 17px; }

  .website { left: 82px; top: 979px; color: var(--purple); font-weight: 700; font-size: 14px; }

  .tile { width: 137px; height: 137px; border: 1px solid var(--frame); background: var(--white); }
  .tile-fill { position: absolute; left: 9px; top: 9px; width: 118px; height: 118px; background: var(--placeholder); font-size: 12px; color: var(--ink); display: flex; align-items: center; padding-left: 12px; }
  .tile-city { background: linear-gradient(180deg, #3a6fb6 0%, #6a8fcf 45%, #2c3550 70%, #1a2236 100%); }
  .tile-label { font-size: 12px; color: var(--ink); }
</style>
</head>
<body>
  <main class="flyer">
    <svg class="flyer-shapes" width="785" height="1015" viewBox="0 0 785 1015">
      <defs>
        <linearGradient id="team-tones" x1="0" y1="0" x2="1" y2="1">
          <stop offset="0" stop-color="#eef1f3"/>
          <stop offset=".5" stop-color="#c9d4de"/>
          <stop offset="1" stop-color="#8ea2b8"/>
        </linearGradient>
      </defs>
      <polygon points="0,0 580,0 335,408 0,408" fill="url(#team-tones)" role="img" aria-label="Photo of three smiling young professionals working at a laptop"/>
      <polygon points="590,0 785,0 785,27 575,27" fill="var(--purple)"/>
      <polygon points="488,178 755,178 755,213 468,213" fill="var(--yellow)"/>
      <polygon points="470,213 785,213 785,538 385,538 360,563 0,563 0,416 348,416" fill="var(--purple)"/>
      <polygon points="0,563 360,563 385,538 785,538 785,578 725,578 700,605 0,605" fill="var(--yellow)"/>
      <polygon points="0,961 365,961 392,991 785,991 785,1015 0,1015" fill="var(--yellow)"/>
    </svg>

    <div class="abs brand">
      <span class="brand-mark"></span>
      <div class="brand-name">ORVELL GLOBAL<br>SERVICES</div>
    </div>

    <div class="abs strap">NEW ZEALAND’S BEST MIGRATION ADVISOR</div>

    <h1 class="abs headline">PROPOSAL<br>TO REPRESENT<br>YOUR INSTITUTION</h1>

    <p class="abs intro">ORV Services Limited is a New Zealand based company established in 2013, engaged in providing end-to-end study abroad and migration services to international students and families. Headed by a Licensed Immigration Adviser with a strong social media presence and a sales &amp; service team operating from different parts of the world. ORV has been servicing clients from more than 30 countries of the world like India, Sri Lanka, Maldives, UAE, Egypt, Brazil, etc. The company boasts of being a specialist in New Zealand student enrollment and also offers after arrival support by an experienced and efficient onshore team.</p>

    <div class="abs services"><span>STUDY</span><span>WORK</span><span>BUSINESS</span><span>TOURS</span></div>

    <p class="abs about">ORV is proud to have successfully served all the leading New Zealand Institutions. Having spent over a decade in this pursuit and realizing the ever increasing growth of study abroad aspirants, the core team of ORV is now keen to expand into other countries and set a global footprint in overseas education domain. Our consistent and creative social media marketing initiatives are attracting topnotch students from different countries to study in high quality global institutions.</p>

    <h2 class="abs tab tab-why">WHY PARTNER WITH US?</h2>
    <ul class="abs reasons">
      <li class="reason"><span class="reason-icon">ICON</span><span class="reason-text">PROVEN TRACK RECORD OF STUDENT<br>ENROLLMENT FOR NEW ZEALAND</span></li>
      <li class="reason"><span class="reason-icon">ICON</span><span class="reason-text">HIGH CONVERSION RATE -<br>APPLICATION TO ENROLMENT</span></li>
      <li class="reason"><span class="reason-icon">ICON</span><span class="reason-text">QUALIFIED AND EXPERIENCED TEAM<br>ACROSS COUNTRIES</span></li>
    </ul>

    <div class="abs website">WWW.ORVELLGLOBAL.COM</div>

    <h2 class="abs tab tab-nz">MY NEW ZEALAND</h2>

    <div class="abs tile" style="left:442px; top:655px;"><div class="tile-fill tile-city" role="img" aria-label="City skyline at dusk reflected in the harbour"></div></div>
    <div class="abs tile" style="left:604px; top:655px;"><div class="tile-fill">PHOTO</div></div>
    <div class="abs tile" style="left:442px; top:824px;"><div class="tile-fill">PHOTO</div></div>
    <div class="abs tile" style="left:604px; top:824px;"><div class="tile-fill">PHOTO</div></div>

    <div class="abs tile-label" style="left:442px; top:797px;">MODERN</div>
    <div class="abs tile-label" style="left:606px; top:797px;">BEAUTIFUL</div>
    <div class="abs tile-label" style="left:442px; top:967px;">PEACEFUL</div>
    <div class="abs tile-label" style="left:606px; top:967px;">INVITING</div>
  </main>
</body>
</html>
```